Velmora Consulting Business

** Please add the content information from my old business card
1. I would like to see a two sided business card with both options with the 1st Option--Tallow Spire-new WHITE BACKGROUND LOGO
2 nd Option-Tallow Spire - new BLACK- Background Logo
3rd -Option a business card with my Photo on the card
Please add the new word to the card information:
EXECUTION
AS THE OWNER'S REP
WE AIM TO ACHIEVE YOUR
INFRASTRUCTURE VISION with
OUR SPECIALIZATION & EXECUTION in:

FUNDING Planning
BUSINESS Planning
INFRASTRUCTURE Planning
PROJECT Management
Since 2012
_____________________________________________________________________
I want to get spot uv raised printing. I was liking a a nice rich white linen paper stock with black writing & NOT A COLORED CARD other than a variety of white or black cards concept

```html
<!DOCTYPE html>
<html lang="en">
<head>
<meta charset="utf-8">
<title>Velmora Consulting – Business Card</title>
<link rel="stylesheet" href="https://fonts.googleapis.com/css2?family=Source+Sans+3:wght@400;600;700&display=swap">
<style>
  :root {
    --backdrop: #9a9a9a;
    --card-white: #f2f2f2;
    --card-black: #0c0c0c;
    --ink: #1f1f1f;
    --paper-ink: #f4f4f4;
    --accent: #e0213b;
    --rule: #8a8a8a;
  }
  * { margin: 0; padding: 0; box-sizing: border-box; }
  html, body {
    width: 1093px; height: 1200px; overflow: hidden;
    background: var(--backdrop);
    font-family: "Source Sans 3", "Myriad Pro", sans-serif;
  }
  .card {
    position: absolute;
    left: 264px;
    width: 580px;
    height: 358px;
    overflow: hidden;
  }
  .card--front { top: 226px; background: var(--card-white); color: var(--ink); }
  .card--back { top: 620px; background: var(--card-black); color: var(--paper-ink); }

  .brand { position: absolute; font-weight: 700; line-height: 1; }
  .brand__name { display: block; font-size: 56px; letter-spacing: -1.5px; }
  .brand__tag { display: block; font-size: 16px; letter-spacing: 13.4px; margin-top: 10px; }
  .card--front .brand { left: 28px; top: 56px; color: var(--ink); }
  .card--back .brand { left: 57px; top: 172px; color: var(--paper-ink); }
  .card--back .brand__name { font-size: 46px; }
  .card--back .brand__tag { font-size: 13px; letter-spacing: 11.2px; margin-top: 8px; }

  .person { position: absolute; left: 27px; top: 170px; line-height: 1.2; }
  .person__name { font-size: 21px; font-weight: 600; }
  .person__role { font-size: 15.5px; color: var(--accent); margin-top: 0; }

  .contacts { position: absolute; left: 27px; top: 226px; list-style: none; font-size: 16.5px; }
  .contacts li { display: flex; align-items: center; height: 21px; }
  .contacts svg { width: 15px; height: 15px; margin-right: 9px; fill: none; stroke: var(--ink); stroke-width: 1.6; }

  .locations { position: absolute; left: 27px; top: 306px; font-size: 16.5px; }
  .locations .dot { color: var(--accent); margin: 0 3px; }

  .statement {
    position: absolute; left: 301px; top: 135px;
    font-size: 15px; line-height: 18.4px;
  }

  .rule { position: absolute; left: 30px; width: 511px; height: 1px; background: var(--rule); }
  .rule--top { top: 259px; }
  .rule--bottom { top: 320px; }

  .services {
    position: absolute; left: 84px; top: 272px;
    display: grid; grid-template-columns: 208px auto;
    list-style: none; font-size: 15px; line-height: 18.4px;
  }
  .services li { display: flex; align-items: center; }
  .services li::before {
    content: ""; width: 8px; height: 8px; background: var(--accent); margin-right: 10px;
  }

  .since { position: absolute; left: 0; right: 0; top: 326px; text-align: center; font-size: 15px; }
</style>
</head>
<body>
  <section class="card card--front" aria-label="Card front">
    <div class="brand">
      <span class="brand__name">Velmora</span>
      <span class="brand__tag">CONSULTING</span>
    </div>
    <div class="person">
      <p class="person__name">Renata Halloway-Brisk</p>
      <p class="person__role">CEO / LEAD PROJECT MANAGER</p>
    </div>
    <ul class="contacts">
      <li><svg viewBox="0 0 16 16"><path d="M4 2l3 3-2 2c1 2 2 3 4 4l2-2 3 3-2 2C7 14 2 9 2 4z"/></svg>867.555.0184</li>
      <li><svg viewBox="0 0 16 16"><rect x="1.5" y="3.5" width="13" height="9"/><path d="M1.5 3.5l6.5 5 6.5-5"/></svg>renata@velmora.ca</li>
      <li><svg viewBox="0 0 16 16"><circle cx="8" cy="8" r="6.5"/><ellipse cx="8" cy="8" rx="3" ry="6.5"/><path d="M1.5 8h13M2.5 5h11M2.5 11h11"/></svg>www.velmora.ca</li>
    </ul>
    <p class="locations">Northvale NT<span class="dot">•</span>Kellmere Falls NB</p>
  </section>

  <section class="card card--back" aria-label="Card back">
    <div class="brand">
      <span class="brand__name">Velmora</span>
      <span class="brand__tag">CONSULTING</span>
    </div>
    <p class="statement">
      EXECUTION<br>
      AS THE OWNER'S REP<br>
      WE AIM TO ACHIEVE YOUR<br>
      INFRASTRUCTURE VISION with<br>
      OUR SPECIALIZATION &amp; EXECUTION in:
    </p>
    <div class="rule rule--top"></div>
    <ul class="services">
      <li>FUNDING Planning</li>
      <li>BUSINESS Planning</li>
      <li>INFRASTRUCTURE Planning</li>
      <li>PROJECT Management</li>
    </ul>
    <div class="rule rule--bottom"></div>
    <p class="since">Since 2012</p>
  </section>
</body>
</html>
```